We need professional looking business cards for our e-assessment business based in Europe. Our company is called Velmo.

You can just use sample name and addresses.

The colours we use are:

#70abe4 (blue)
#FF6600 (orange)

The back side should say: Online testing, simply done

This is the print-shop we are using. Please look at the link for info about formats: http://nl.prindavo.com/help/faq/using-my-own-artwork.html

Target market is education and large corporations

Business

```html
<!DOCTYPE html>
<html lang="en">
<head>
<meta charset="utf-8">
<title>Velmo business cards</title>
<link rel="stylesheet" href="https://fonts.googleapis.com/css2?family=Questrial&display=swap">
<style>
  :root {
    --brand-orange: #ff6600;
    --brand-blue: #70abe4;
    --card-dark: #2b2b2b;
    --card-dark-edge: #1f1f1f;
    --card-light: #ffffff;
    --card-light-edge: #ececec;
    --ink-dark: #3a3a3a;
    --ink-muted: #5a5a5a;
    --ink-on-dark: #d9d9d9;
    --backdrop: #e4e4e2;
  }
  * { box-sizing: border-box; margin: 0; padding: 0; }
  html, body { width: 1200px; height: 871px; overflow: hidden; }
  body {
    background: var(--backdrop);
    font-family: "Questrial", sans-serif;
    position: relative;
  }
  .card {
    position: absolute;
    width: 520px;
    height: 336px;
    border-radius: 3px;
    box-shadow: 0 10px 28px rgba(0,0,0,0.22);
  }
  .card--back {
    left: 45px;
    top: 268px;
    background: linear-gradient(160deg, var(--card-dark) 0%, var(--card-dark-edge) 100%);
  }
  .card--front {
    left: 635px;
    top: 268px;
    background: linear-gradient(160deg, var(--card-light) 55%, var(--card-light-edge) 100%);
  }
  .wordmark {
    display: flex;
    align-items: center;
    gap: 14px;
  }
  .wordmark__dot {
    border-radius: 50%;
    background: var(--brand-orange);
    flex: none;
  }
  .wordmark__name { line-height: 1; letter-spacing: 0.5px; }

  .card--back .wordmark {
    position: absolute;
    left: 50%;
    top: 108px;
    transform: translateX(-50%);
  }
  .card--back .wordmark__dot { width: 50px; height: 50px; }
  .card--back .wordmark__name { font-size: 46px; color: var(--ink-on-dark); }
  .tagline {
    position: absolute;
    left: 0; right: 0;
    top: 200px;
    text-align: center;
    color: var(--brand-blue);
    font-size: 22px;
    letter-spacing: 2.5px;
    word-spacing: 6px;
    white-space: nowrap;
  }

  .card--front .wordmark {
    position: absolute;
    left: 34px;
    top: 214px;
  }
  .card--front .wordmark__dot { width: 58px; height: 58px; }
  .card--front .wordmark__name { font-size: 56px; color: var(--ink-dark); }
  .contact {
    position: absolute;
    left: 318px;
    top: 218px;
    color: var(--ink-muted);
    font-size: 13px;
    font-style: normal;
    line-height: 1.55;
    letter-spacing: 0.6px;
    white-space: nowrap;
  }
  .contact__name { font-size: 18px; color: var(--ink-dark); letter-spacing: 1.5px; margin-bottom: 4px; }
  .contact__company { color: var(--brand-orange); }
</style>
</head>
<body>
  <section class="card card--back" aria-label="Card back">
    <div class="wordmark">
      <span class="wordmark__dot"></span>
      <span class="wordmark__name">velmo</span>
    </div>
    <p class="tagline">Online testing, simply done</p>
  </section>

  <section class="card card--front" aria-label="Card front">
    <div class="wordmark">
      <span class="wordmark__dot"></span>
      <span class="wordmark__name">velmo</span>
    </div>
    <address class="contact">
      <div class="contact__name">Mara K Olsen</div>
      <div class="contact__company">velmo Inc</div>
      <div>18 Lindon Street, Haarveld</div>
      <div>NH 2031</div>
    </address>
  </section>
</body>
</html>
```